SkyvornQ Business Cards and Stationary Design

Need a design for our business cards and stationary. I want to carry on the theme of the logo. I want the business cards to have a design on the back. I would like the business cards and the stationary to carry the same theme, design scheme, and branding

Target Market(s)

Airlines and Maintenance Facilities

Industry/Entity Type

Aviation

Contact Information for Business Card

Name
Position Title
Address: 4827 Trellis Hollow Road, Fort Pierce, Florida, 34951
Office Number
Mobile Number
Email
Website

Font styles to use
Serif
Sans Serif

Colors

Designer to choose colors to be used in the design.

```html
<!DOCTYPE html>
<html lang="en">
<head>
<meta charset="utf-8">
<title>SkyvornQ Business Card</title>
<link href="https://fonts.googleapis.com/css2?family=Open+Sans:wght@400;600;700&display=swap" rel="stylesheet">
<style>
  :root {
    --stage: #1b1b1b;
    --card-light: #f3f3f3;
    --navy: #0d1f45;
    --brand-blue: #1467b3;
    --text-grey: #333a40;
    --blue-deep: #0b4f94;
    --blue-mid: #0a78c4;
    --blue-glow: #0a9ce6;
    --white: #ffffff;
  }
  * { margin: 0; padding: 0; box-sizing: border-box; }
  html, body { width: 1200px; height: 900px; overflow: hidden; }
  body {
    background: var(--stage);
    font-family: "Open Sans", Arial, sans-serif;
    position: relative;
  }
  .card {
    position: absolute;
    top: 200px;
    width: 310px;
    height: 502px;
    box-shadow: 3px 4px 6px rgba(0,0,0,0.55);
    overflow: hidden;
  }
  .card-front {
    left: 253px;
    background: var(--card-light);
    border-radius: 62px 0 62px 0;
  }
  .card-back {
    left: 627px;
    border-radius: 0 62px 0 62px;
    background:
      radial-gradient(circle at 50% 52%, var(--blue-glow) 0%, var(--blue-mid) 45%, var(--blue-deep) 100%);
  }
  .brand {
    position: absolute;
    left: 0;
    width: 100%;
    text-align: center;
  }
  .front-brand { top: 95px; }
  .brand-ring {
    display: block;
    margin: 0 auto 12px;
    width: 74px;
    height: 74px;
    border-radius: 50%;
    border: 7px solid var(--brand-blue);
  }
  .brand-name {
    font-weight: 700;
    font-size: 29px;
    letter-spacing: 4px;
    color: var(--navy);
  }
  .contact {
    position: absolute;
    left: 34px;
    top: 299px;
    color: var(--text-grey);
    font-size: 14.5px;
    line-height: 18.5px;
  }
  .person-name {
    font-weight: 700;
    font-size: 16px;
    color: var(--brand-blue);
    letter-spacing: 0.3px;
  }
  .person-title { margin-bottom: 7px; }
  .contact-line { display: flex; align-items: center; gap: 6px; }
  .contact-line svg { width: 12px; height: 12px; fill: var(--blue-deep); flex: none; }
  .address { margin-top: 7px; }
  .back-brand { top: 168px; }
  .back-ring {
    display: block;
    margin: 0 auto 18px;
    width: 140px;
    height: 140px;
    border-radius: 50%;
    border: 10px solid var(--white);
  }
  .back-name {
    font-weight: 700;
    font-size: 22px;
    letter-spacing: 4px;
    color: var(--white);
  }
  .back-web {
    position: absolute;
    bottom: 46px;
    width: 100%;
    text-align: center;
    color: var(--white);
    font-weight: 600;
    font-size: 13px;
    letter-spacing: 0.8px;
  }
</style>
</head>
<body>
  <section class="card card-front">
    <div class="brand front-brand">
      <span class="brand-ring"></span>
      <div class="brand-name">SKYVORNQ</div>
    </div>
    <div class="contact">
      <div class="person-name">MARCUS DELANEY</div>
      <div class="person-title">Managing Director</div>
      <div class="contact-line">
        <svg viewBox="0 0 12 12" aria-hidden="true"><path d="M1 4c0-2 2-3 5-3s5 1 5 3l-2 1-1-1.5H4L3 5zM3 6h6l1 5H2z"/></svg>
        <span>044-987 650 321</span>
      </div>
      <div class="contact-line">
        <svg viewBox="0 0 12 12" aria-hidden="true"><path d="M3 0h6v12H3zM4 1.5v8h4v-8z"/></svg>
        <span>044-987 650 321</span>
      </div>
      <div class="contact-line">
        <svg viewBox="0 0 12 12" aria-hidden="true"><path d="M1 2.5h10v7H1zM1.5 3l4.5 3.5L10.5 3"/></svg>
        <span>hello@skyvornq.com</span>
      </div>
      <div class="contact-line">
        <svg viewBox="0 0 12 12" aria-hidden="true"><circle cx="6" cy="6" r="5.5"/></svg>
        <span>www.skyvornq.com</span>
      </div>
      <div class="address">4827 Trellis Hollow Road<br>Fort Pierce, Florida, 34951</div>
    </div>
  </section>

  <section class="card card-back">
    <div class="brand back-brand">
      <span class="back-ring"></span>
      <div class="back-name">SKYVORNQ</div>
    </div>
    <div class="back-web">www.skyvornq.com</div>
  </section>
</body>
</html>
```